brovlanepass.net

Develop a website for brolanepass.net will be a site to sell tickets for concerts, shows, shows, theaters and others. I need a web design easy view, very easy to use and accumulate events by date. The aim is to develop the site was connected to a complex system that is already developed. (Important this page to a robust system was connected via links the idea is to develop only the front view)
Updates

Reason: I need more designs yet we have not made the decision

Target Market(s)

millennials, adults, who want to enjoy concerts and shows

Industry/Entity Type

Event

Number of Pages Required

5+ page

Colors
1b1b1b
aaaaaa
ffffff

Requirements
Must have
• Easy Vista, accumulation of upcoming events, past events. The tabs should have are: 1 Start: In this part of upcoming events occur. You could put a banner on the top and down the events by date. 2. How to order: page with instructions on how to purchase tickets 3. About Us: The company history 4. Contact: Phones and template for contact by mail 5. Our policies: shopping 6. Notice Privacy: Privacy Notice Copoy 7. Centers Sale: physical places where they can purchase tickets Promoters 8. access: Link to a template
Nice to have
• as you can see p www.quimbarostage.net or farunda.net or farunda.org or gallowmerk.net (important this page to a robust system was connected via links the idea is to develop only the front view)
Should not have
• Many things Tangled

```html
<!DOCTYPE html>
<html lang="en">
<head>
<meta charset="utf-8">
<title>Brovlanepass — Tickets for concerts, shows and theatres</title>
<link rel="stylesheet" href="https://fonts.googleapis.com/css2?family=Barlow:wght@400;500;600;700;800&family=Barlow+Semi+Condensed:wght@600;700;800&display=swap">
<style>
:root{
  --ink:#1b1b1b;
  --ink-soft:#2b2b2b;
  --grey:#aaaaaa;
  --grey-mid:#6e6e6e;
  --panel:#f6f6f6;
  --line:#e3e3e3;
  --white:#ffffff;
  --head:"Barlow Semi Condensed", "Barlow", sans-serif;
  --body:"Barlow", sans-serif;
}
*{box-sizing:border-box;margin:0;padding:0}
html,body{width:1200px;height:3704px;overflow:hidden;background:var(--white);color:var(--ink);font-family:var(--body)}
.page{position:relative;width:1200px;height:3704px;overflow:hidden}
.abs{position:absolute}

/* header */
.site-header{position:absolute;left:0;top:0;width:1200px;height:74px;z-index:5}
.header-light{position:absolute;left:0;top:0;width:520px;height:74px;background:var(--white);clip-path:polygon(0 0,100% 0,88% 100%,0 100%)}
.brand{position:absolute;left:215px;top:22px;font-family:var(--head);font-weight:800;font-size:30px;letter-spacing:.5px;color:var(--ink);display:flex;align-items:center;gap:10px}
.brand-mark{width:12px;height:12px;background:var(--ink)}
.main-nav{position:absolute;left:490px;top:0;height:74px;display:flex;align-items:center;gap:24px;padding-left:6px}
.main-nav a{font-family:var(--head);font-weight:700;font-size:13px;color:var(--white);text-decoration:none;letter-spacing:.4px}

/* hero */
.hero{position:absolute;left:0;top:0;width:1200px;height:716px;clip-path:polygon(0 0,100% 0,100% 100%,0 86%)}
.hero-photo{position:absolute;inset:0;background:
  radial-gradient(ellipse 520px 320px at 820px 120px,#9a9a9a 0%,#4a4a4a 45%,transparent 75%),
  radial-gradient(ellipse 700px 300px at 600px 700px,#0c0c0c 0%,transparent 80%),
  linear-gradient(180deg,#3a3a3a 0%,#1e1e1e 55%,#0e0e0e 100%)}
.hero-kicker{position:absolute;left:225px;top:300px;font-family:var(--head);font-weight:700;font-size:15px;color:var(--white);letter-spacing:.5px}
.hero-title{position:absolute;left:222px;top:320px;font-family:var(--head);font-weight:800;font-size:58px;line-height:56px;color:var(--white);letter-spacing:.5px}
.hero-title .muted{color:var(--grey-mid)}
.hero-sub{position:absolute;left:225px;top:448px;font-family:var(--head);font-weight:700;font-size:20px;color:var(--white);letter-spacing:.6px}
.btn-hero{position:absolute;left:225px;top:501px;width:173px;height:55px;background:#5a5a5a;color:var(--white);font-family:var(--head);font-weight:700;font-size:14px;display:flex;align-items:center;justify-content:center;letter-spacing:.5px}
.slider-dots{position:absolute;left:882px;top:554px;display:flex;gap:16px}
.slider-dots span{width:12px;height:12px;border-radius:50%;background:#8c8c8c}
.slider-dots span.active{background:var(--white)}

/* section titles */
.section-title{position:absolute;left:0;width:1200px;text-align:center;font-family:var(--head);font-weight:800;font-size:27px;letter-spacing:.6px}

/* featured grid */
.featured-grid{position:absolute;left:215px;top:818px;width:770px;height:429px;display:grid;grid-template-columns:repeat(3,1fr);grid-template-rows:repeat(2,1fr)}
.tile-photo{position:relative;display:flex;align-items:center;justify-content:center}
.date-badge{width:80px;height:78px;background:rgba(30,30,30,.72);color:var(--white);font-family:var(--head);font-weight:800;font-size:17px;line-height:19px;text-align:center;display:flex;flex-direction:column;justify-content:center}
.date-badge .yr{color:var(--grey)}
.tile-text{padding:30px 20px 0 14px;background:var(--white)}
.posted{font-family:var(--head);font-weight:700;font-size:9px;color:var(--grey);letter-spacing:.6px}
.tile-text h3{margin-top:8px;font-family:var(--head);font-weight:800;font-size:17px;line-height:19px;color:var(--ink)}
.btn-outline{display:inline-flex;align-items:center;justify-content:center;margin-top:18px;width:94px;height:32px;border:2px solid var(--ink);font-family:var(--head);font-weight:700;font-size:10px;color:var(--ink);letter-spacing:.4px}

/* upcoming */
.filter-bar{position:absolute;left:215px;top:1366px;width:770px;height:84px;border:1px solid var(--line);display:flex;align-items:center;padding:0 18px 0 14px}
.filter-bar h2{font-family:var(--head);font-weight:800;font-size:26px;letter-spacing:.5px;flex:1}
.filter{display:flex;align-items:center;gap:10px;margin-left:24px;font-family:var(--head);font-weight:800;font-size:13px}
.filter .val{font-weight:600;font-size:10px;color:var(--grey)}
.event-card{position:absolute;left:215px;width:770px;height:301px}
.event-panel{position:absolute;left:155px;top:0;width:615px;height:301px;background:var(--panel)}
.event-photo{position:absolute;left:0;top:40px;width:333px;height:222px}
.event-date{position:absolute;left:0;top:266px;font-family:var(--head);font-weight:800;font-size:17px}
.event-body{position:absolute;left:363px;top:52px;width:380px}
.event-body h3{margin-top:10px;font-family:var(--head);font-weight:800;font-size:17px;line-height:20px}
.event-body p{margin-top:14px;font-size:10px;line-height:15px;color:#777}
.event-body .btn-outline{margin-top:18px}

/* theatres */
.theatres{position:absolute;left:0;top:2590px;width:1200px;height:845px;clip-path:polygon(0 14%,100% 0,100% 88%,0 100%)}
.theatres-bg{position:absolute;inset:0;background:
  radial-gradient(ellipse 600px 380px at 820px 520px,#3a3a3a 0%,transparent 75%),
  linear-gradient(180deg,#1e1e1e 0%,#222 60%,#161616 100%)}
.theatres .section-title{color:var(--white);top:150px}
.show-card{position:absolute;top:283px;width:368px;height:343px;border:1px solid #777}
.show-photo{position:absolute;left:31px;top:-45px;width:302px;height:228px}
.show-body{position:absolute;left:31px;top:198px;width:310px}
.show-body .posted{color:var(--white)}
.show-body h3{margin-top:10px;font-family:var(--head);font-weight:800;font-size:17px;line-height:20px;color:var(--white)}
.show-body .btn-outline{border:1px solid #999;color:var(--white);font-size:10px;width:94px;height:32px}
.carousel-arrows{position:absolute;left:575px;top:668px;display:flex;gap:20px}

/* footer */
.footer-col{position:absolute;top:3408px}
.footer-col h4{font-family:var(--head);font-weight:800;font-size:12px;letter-spacing:.4px;margin-bottom:16px}
.footer-col li{list-style:none;font-family:var(--head);font-weight:700;font-size:12px;line-height:21px;letter-spacing:.3px}
.footer-brand{position:absolute;left:215px;top:3508px;font-family:var(--head);font-weight:800;font-size:21px;display:flex;align-items:center;gap:8px}
.footer-brand .brand-mark{width:9px;height:9px}
.social{display:flex;gap:8px;margin-top:10px}
.social span{width:20px;height:20px;border-radius:50%;background:var(--ink)}
.footer-rule{position:absolute;left:0;top:3650px;width:1200px;height:1px;background:var(--line)}
.copyright{position:absolute;left:0;width:1200px;top:3668px;text-align:center;font-family:var(--head);font-weight:700;font-size:10px;letter-spacing:.4px}
.corner-tag{position:absolute;right:20px;top:3666px;font-family:var(--head);font-weight:700;font-size:10px;color:var(--grey)}
</style>
</head>
<body>
<div class="page">

  <section class="hero">
    <div class="hero-photo" role="img" aria-label="Concert crowd with raised hands under bright stage lights, in black and white"></div>
    <div class="hero-kicker">CONCERT SHOW 2017</div>
    <h1 class="hero-title">MUSIC CONCERT<br><span class="muted">IN LONDON</span></h1>
    <div class="hero-sub">WE SELL TICKETS ON MARCH 25TH | 2017</div>
    <a class="btn-hero">BUY TICKETS</a>
    <div class="slider-dots"><span class="active"></span><span></span><span></span><span></span></div>
  </section>

  <header class="site-header">
    <div class="header-light"></div>
    <div class="brand"><span class="brand-mark"></span>BROVLANEPASS</div>
    <nav class="main-nav">
      <a>HOME</a><a>HOW TO ORDER</a><a>ABOUT US</a><a>CONTACT US</a><a>POLICIES</a><a>PRIVACY</a><a>CENTER SALE</a><a>ACCESS</a>
    </nav>
  </header>

  <h2 class="section-title" style="top:722px">FEATURED CONCERTS</h2>
  <div class="featured-grid">
    <div class="tile-photo" role="img" aria-label="Concert photo with a crowd in front of a white-lit stage" style="background:linear-gradient(135deg,#f3ece8 0%,#c4a9a0 45%,#5a3b3a 100%)">
      <div class="date-badge">MARCH<br>17TH<br><span class="yr">2017</span></div>
    </div>
    <div class="tile-text">
      <div class="posted">POSTED BY BROVLANEPASS</div>
      <h3>NEQUE PORRO QUISQUAM EST QUI DOLOREM IPSUM QUIA DOLOR SIT AMET, CONSECTETUR ...</h3>
      <span class="btn-outline">BUY TICKETS</span>
    </div>
    <div class="tile-photo" role="img" aria-label="Concert photo with a crowd under purple stage lights" style="background:linear-gradient(135deg,#3a2a7a 0%,#8a63c8 45%,#1e1840 100%)">
      <div class="date-badge">MARCH<br>17TH<br><span class="yr">2017</span></div>
    </div>
    <div class="tile-text">
      <div class="posted">POSTED BY BROVLANEPASS</div>
      <h3>NEQUE PORRO QUISQUAM EST QUI DOLOREM IPSUM QUIA DOLOR SIT AMET, CONSECTETUR ...</h3>
      <span class="btn-outline">BUY TICKETS</span>
    </div>
    <div class="tile-photo" role="img" aria-label="Guitarist playing on a red and blue lit stage" style="background:linear-gradient(135deg,#7a1a22 0%,#3a1c3a 50%,#1a2a6a 100%)">
      <div class="date-badge">MARCH<br>17TH<br><span class="yr">2017</span></div>
    </div>
    <div class="tile-text">
      <div class="posted">POSTED BY BROVLANEPASS</div>
      <h3>NEQUE PORRO QUISQUAM EST QUI DOLOREM IPSUM QUIA DOLOR SIT AMET, CONSECTETUR ...</h3>
      <span class="btn-outline">BUY TICKETS</span>
    </div>
  </div>

  <div class="filter-bar">
    <h2>UPCOMING EVENTS</h2>
    <div class="filter">MONTH <span class="val">MARCH</span>
      <svg width="8" height="14" viewBox="0 0 8 14"><path d="M4 1 7 5H1zM4 13 1 9h6z" fill="#1b1b1b"/></svg></div>
    <div class="filter">DAY <span class="val">26TH SUNDAY</span>
      <svg width="8" height="14" viewBox="0 0 8 14"><path d="M4 1 7 5H1zM4 13 1 9h6z" fill="#1b1b1b"/></svg></div>
    <div class="filter">YEAR <span class="val">2017</span>
      <svg width="8" height="14" viewBox="0 0 8 14"><path d="M4 1 7 5H1zM4 13 1 9h6z" fill="#1b1b1b"/></svg>
      <svg width="16" height="16" viewBox="0 0 16 16" style="margin-left:8px"><rect x="1" y="3" width="14" height="12" fill="none" stroke="#1b1b1b" stroke-width="2"/><rect x="1" y="3" width="14" height="4" fill="#1b1b1b"/><path d="M4 1v4M12 1v4" stroke="#1b1b1b" stroke-width="2"/><path d="M4 10h2M7 10h2M10 10h2M4 12.5h2M7 12.5h2" stroke="#1b1b1b" stroke-width="1.5"/></svg></div>
  </div>

  <article class="event-card" style="top:1497px">
    <div class="event-panel"></div>
    <div class="event-photo" role="img" aria-label="Crowd facing a stage glowing with orange light" style="background:radial-gradient(ellipse at 55% 30%,#ffd27a 0%,#e0642a 35%,#5a1a0a 80%)"></div>
    <div class="event-date">MARCH 26TH | 2017</div>
    <div class="event-body">
      <div class="posted">POSTED BY BROVLANEPASS</div>
      <h3>NEQUE PORRO QUISQUAM EST QUI DOLOREM IPSUM QUIA DOLOR SIT AMET, CONSECTETUR ...</h3>
      <p>Sed ut perspiciatis unde omnis iste natus error sit voluptatem accusantium doloremque laudantium, totam rem aperiam, eaque ipsa quae ab illo inventore veritatis et quasi architecto beatae vitae dicta</p>
      <span class="btn-outline">BUY TICKETS</span>
    </div>
  </article>

  <article class="event-card" style="top:1848px">
    <div class="event-panel"></div>
    <div class="event-photo" role="img" aria-label="Dancers performing on a stage lit in blue and purple" style="background:linear-gradient(135deg,#1a2a8a 0%,#5a3aa0 50%,#0e0e3a 100%)"></div>
    <div class="event-date">MARCH 26TH | 2017</div>
    <div class="event-body">
      <div class="posted">POSTED BY BROVLANEPASS</div>
      <h3>NEQUE PORRO QUISQUAM EST QUI DOLOREM IPSUM QUIA DOLOR SIT AMET, CONSECTETUR ...</h3>
      <p>Sed ut perspiciatis unde omnis iste natus error sit voluptatem accusantium doloremque laudantium, totam rem aperiam, eaque ipsa quae ab illo inventore veritatis et quasi architecto beatae vitae dicta</p>
      <span class="btn-outline">BUY TICKETS</span>
    </div>
  </article>

  <article class="event-card" style="top:2198px">
    <div class="event-panel"></div>
    <div class="event-photo" role="img" aria-label="Band with drummer playing on a stage under teal and warm lights" style="background:linear-gradient(135deg,#1f4a5a 0%,#2a3040 50%,#7a3a2a 100%)"></div>
    <div class="event-date">MARCH 26TH | 2017</div>
    <div class="event-body">
      <div class="posted">POSTED BY BROVLANEPASS</div>
      <h3>NEQUE PORRO QUISQUAM EST QUI DOLOREM IPSUM QUIA DOLOR SIT AMET, CONSECTETUR ...</h3>
      <p>Sed ut perspiciatis unde omnis iste natus error sit voluptatem accusantium doloremque laudantium, totam rem aperiam, eaque ipsa quae ab illo inventore veritatis et quasi architecto beatae vitae dicta</p>
      <span class="btn-outline">BUY TICKETS</span>
    </div>
  </article>

  <section class="theatres">
    <div class="theatres-bg" role="img" aria-label="Empty theatre auditorium with rows of seats, in dark grey tones"></div>
    <h2 class="section-title">THEATRES</h2>
    <article class="show-card" style="left:225px">
      <div class="show-photo" role="img" aria-label="Dancer posing on a stage in blue light" style="background:linear-gradient(160deg,#6aa0c8 0%,#2a5a8a 50%,#0e1e3a 100%)"></div>
      <div class="show-body">
        <div class="posted">POSTED BY BROVLANEPASS</div>
        <h3>NEQUE PORRO QUISQUAM EST QUI DOLOREM IPSUM QUIA ...</h3>
        <span class="btn-outline">BUY TICKETS</span>
      </div>
    </article>
    <article class="show-card" style="left:608px">
      <div class="show-photo" role="img" aria-label="Theatre performer in a masked costume, red and warm tones" style="background:linear-gradient(160deg,#8a2a2a 0%,#c8743a 50%,#2a1a1a 100%)"></div>
      <div class="show-body">
        <div class="posted">POSTED BY BROVLANEPASS</div>
        <h3>NEQUE PORRO QUISQUAM EST QUI DOLOREM IPSUM QUIA ...</h3>
        <span class="btn-outline">BUY TICKETS</span>
      </div>
    </article>
    <div class="carousel-arrows">
      <svg width="14" height="22" viewBox="0 0 14 22"><path d="M11 2 3 11l8 9" fill="none" stroke="#fff" stroke-width="3"/></svg>
      <svg width="14" height="22" viewBox="0 0 14 22"><path d="M3 2l8 9-8 9" fill="none" stroke="#fff" stroke-width="3"/></svg>
    </div>
  </section>

  <footer>
    <div class="footer-brand"><span class="brand-mark"></span>BROVLANEPASS</div>
    <div class="footer-col" style="left:457px">
      <h4>QUICK LINKS</h4>
      <ul><li>HOME</li><li>HOW TO ORDER</li><li>ABOUT US</li><li>CONTACT US</li><li>POLICIES</li><li>PRIVACY</li><li>CENTER SALE</li><li>ACCESS</li></ul>
    </div>
    <div class="footer-col" style="left:640px">
      <h4>OTHER LINKS</h4>
      <ul><li>YOUR ACCOUNT</li><li>TRANSFER OR SELL TICKETS</li><li>PRINT TICKETS</li><li>FAQS</li><li>REFUNDS AND EXCHANGES</li><li>GET HELP</li><li>CUSTOM TICKETS</li><li>GIFT CARDS</li></ul>
    </div>
    <div class="footer-col" style="left:867px">
      <h4>SUPPORT LINKS</h4>
      <ul><li>TERMS OF USE</li><li>HELP</li><li>DISCLAIMER</li></ul>
      <h4 style="margin-top:14px;margin-bottom:0">CONNECT WITH US</h4>
      <div class="social"><span></span><span></span><span></span></div>
    </div>
    <div class="footer-rule"></div>
    <div class="copyright">© 2017 COMPANY NAME | ALL RIGHTS RESERVED</div>
    <div class="corner-tag">CS</div>
  </footer>

</div>
</body>
</html>
```